Push notification screens at app start up

We have an existing news publication app platform and are adding categories to push notifications.

We need two screens designed (each for Zorbel, Quillet and Android for a total of 6d) that show when the app is first launched.

The workflow of our app:
0. app launch screen while webservices run (no work needed)
1. information screen to the user promoting the benefits of push notification with "Next" button. (see concept attached)
2. Push categories selection screen. This will have list of category types, with on/off switch.

"Select the categories that you wish to receive occasional notices:
Breaking News (on/off switch)
Local News (on/off switch)
Sports (on/off switch)
Local Events (on/off switch)
Weather Alerts (on/off switch)
Local Deals (on/off switch)"

"Enable these categories on the next screen."
"Next" button

Background:
When I was looking around at app designs, I came across this one (http://www.plinthworks.example/design/7719034) and I really liked it. We obviously have different features on our screen, but I’d like to have this same feel. The colors used in this design are perfect.

UPDATE: I do not mean to limit your design to match the layout as the one mentioned above. Please use your creativity for the layout.

Our standard font in Helvetica Neue.

Notes:
- our app is developed for all phone devices from Zorbel 4 to Zorbel 6, so designs should be thoughtful of vertical scrolling if needed.
- our app is developed for Quillets, so we'll need designs completed as well. (We can finalize Zorbel design first, then translate the design to Quillet.)
- our app is developed for Android phones (not tablets), so we'll need designs completed as well. (We can finalize iOS design first, then translater to Android UI design guidelines).

We hope to establish a good on-going relationship with the designer for as-needed work in the future.

News

• Helvetica Neue

• Clean designs. No clutter.
• We would likely go with the standard on/off switches for both iOS and Android, but are open to small custom variations.

```html
<!DOCTYPE html>
<html lang="en">
<head>
<meta charset="utf-8">
<title>Notifications</title>
<link rel="stylesheet" href="https://fonts.googleapis.com/css2?family=Inter:wght@400;500;600;700&display=swap">
<style>
  :root {
    --bar-bg: #f7f7f7;
    --screen-black: #000000;
    --row-bg: #ffffff;
    --divider: #e2e2e2;
    --label-grey: #7b7b7b;
    --title-grey: #555555;
    --status-ink: #222222;
    --status-soft: #9a9a9a;
    --icon-grey: #8a8a8a;
    --switch-on: #2f7cf6;
    --switch-off-border: #e4e4e4;
    --knob: #ffffff;
  }
  * { box-sizing: border-box; margin: 0; padding: 0; }
  html, body {
    width: 675px; height: 1200px; overflow: hidden;
    background: var(--screen-black);
    font-family: "Inter", "Helvetica Neue", Arial, sans-serif;
  }
  .screen { position: relative; width: 675px; height: 1200px; background: var(--screen-black); }

  .top-bar { position: absolute; left: 0; top: 0; width: 675px; height: 144px; background: var(--bar-bg); }
  .status-bar {
    position: absolute; left: 0; top: 12px; width: 675px; height: 34px;
    font-size: 19px; font-weight: 500; color: var(--status-ink);
  }
  .status-left { position: absolute; left: 10px; top: 0; display: flex; align-items: center; gap: 8px; height: 34px; }
  .signal { letter-spacing: 0; font-size: 12px; }
  .status-time { position: absolute; left: 0; width: 100%; text-align: center; line-height: 34px; }
  .status-right { position: absolute; right: 12px; top: 0; display: flex; align-items: center; gap: 8px; height: 34px; }

  .nav-title {
    position: absolute; left: 0; top: 68px; width: 100%; text-align: center;
    font-size: 35px; font-weight: 400; color: var(--title-grey); letter-spacing: 0.3px;
  }
  .nav-back { position: absolute; left: 24px; top: 76px; }

  .intro {
    position: absolute; left: 0; top: 144px; width: 675px; height: 155px;
    display: flex; align-items: center; justify-content: center; text-align: center;
    color: #ffffff; font-size: 23.5px; line-height: 32px; font-weight: 400;
  }

  .category-list { position: absolute; left: 0; top: 299px; width: 675px; list-style: none; background: var(--row-bg); }
  .category {
    position: relative; height: 99.5px; display: flex; align-items: center;
    border-bottom: 2px solid var(--divider);
  }
  .category:last-child { border-bottom: none; }
  .category-icon { position: absolute; left: 27px; top: 36px; }
  .category-label {
    position: absolute; left: 101px; font-size: 28px; font-weight: 600; color: var(--label-grey);
  }
  .switch {
    position: absolute; right: 16px; top: 31px; width: 68px; height: 40px;
    border-radius: 20px; border: 2px solid var(--switch-off-border); background: var(--knob);
  }
  .switch::after {
    content: ""; position: absolute; top: 0; left: 0; width: 36px; height: 36px; border-radius: 50%;
    background: var(--knob); box-shadow: 0 2px 4px rgba(0,0,0,0.25), 0 0 0 1px rgba(0,0,0,0.06);
  }
  .switch.is-on { background: var(--switch-on); border-color: var(--switch-on); }
  .switch.is-on::after { left: 28px; }
</style>
</head>
<body>
<div class="screen">
  <header class="top-bar">
    <div class="status-bar">
      <div class="status-left">
        <span class="signal">●●●○○</span>
        <span class="carrier">LARK</span>
        <svg width="22" height="16" viewBox="0 0 24 18" aria-hidden="true">
          <path d="M12 17 L8 12.5 A6 6 0 0 1 16 12.5 Z" fill="var(--status-ink)"/>
          <path d="M4.5 9 A11 11 0 0 1 19.5 9" stroke="var(--status-ink)" stroke-width="2.4" fill="none"/>
          <path d="M1 5.5 A16 16 0 0 1 23 5.5" stroke="var(--status-ink)" stroke-width="2.4" fill="none"/>
        </svg>
      </div>
      <div class="status-time">4:21 PM</div>
      <div class="status-right">
        <svg width="12" height="20" viewBox="0 0 12 20" aria-hidden="true">
          <path d="M1 5 L10 14 L5.5 18.5 V1.5 L10 6 L1 15" stroke="var(--status-soft)" stroke-width="1.6" fill="none" stroke-linejoin="round"/>
        </svg>
        <span class="battery-level">100%</span>
        <svg width="40" height="18" viewBox="0 0 40 18" aria-hidden="true">
          <rect x="1" y="1" width="34" height="16" rx="3" fill="none" stroke="var(--status-ink)" stroke-width="1.6"/>
          <rect x="3.5" y="3.5" width="29" height="11" rx="1.5" fill="var(--status-ink)"/>
          <rect x="36" y="6" width="3" height="6" rx="1" fill="var(--status-ink)"/>
        </svg>
      </div>
    </div>
    <svg class="nav-back" width="22" height="36" viewBox="0 0 22 36" aria-label="Back">
      <path d="M19 2 L4 18 L19 34" stroke="var(--title-grey)" stroke-width="3.5" fill="none" stroke-linecap="round" stroke-linejoin="round"/>
    </svg>
    <h1 class="nav-title">Notifications</h1>
  </header>

  <p class="intro">Select the categories of notices you<br>wish to receive:</p>

  <ul class="category-list">
    <li class="category">
      <svg class="category-icon" width="40" height="30" viewBox="0 0 40 30" aria-hidden="true">
        <rect x="1.5" y="1.5" width="37" height="27" fill="none" stroke="var(--icon-grey)" stroke-width="2.5"/>
        <rect x="7" y="7" width="10" height="8" fill="var(--icon-grey)"/>
        <path d="M21 8h12M21 13h12M7 19h26M7 23h26" stroke="var(--icon-grey)" stroke-width="2"/>
      </svg>
      <span class="category-label">Breaking News</span>
      <span class="switch" role="switch" aria-checked="false" aria-label="Breaking News"></span>
    </li>
    <li class="category">
      <svg class="category-icon" width="40" height="30" viewBox="0 0 40 30" aria-hidden="true">
        <rect x="1.5" y="1.5" width="37" height="27" fill="none" stroke="var(--icon-grey)" stroke-width="2.5"/>
        <rect x="7" y="7" width="10" height="8" fill="var(--icon-grey)"/>
        <path d="M21 8h12M21 13h12M7 19h26M7 23h26" stroke="var(--icon-grey)" stroke-width="2"/>
      </svg>
      <span class="category-label">Local News</span>
      <span class="switch is-on" role="switch" aria-checked="true" aria-label="Local News"></span>
    </li>
    <li class="category">
      <svg class="category-icon" width="40" height="30" viewBox="0 0 40 30" aria-hidden="true">
        <rect x="1.5" y="1.5" width="37" height="27" fill="none" stroke="var(--icon-grey)" stroke-width="2.5"/>
        <rect x="7" y="7" width="10" height="8" fill="var(--icon-grey)"/>
        <path d="M21 8h12M21 13h12M7 19h26M7 23h26" stroke="var(--icon-grey)" stroke-width="2"/>
      </svg>
      <span class="category-label">Sports</span>
      <span class="switch" role="switch" aria-checked="false" aria-label="Sports"></span>
    </li>
    <li class="category">
      <svg class="category-icon" width="40" height="30" viewBox="0 0 40 30" aria-hidden="true">
        <rect x="1.5" y="1.5" width="37" height="27" fill="none" stroke="var(--icon-grey)" stroke-width="2.5"/>
        <rect x="7" y="7" width="10" height="8" fill="var(--icon-grey)"/>
        <path d="M21 8h12M21 13h12M7 19h26M7 23h26" stroke="var(--icon-grey)" stroke-width="2"/>
      </svg>
      <span class="category-label">Local Events</span>
      <span class="switch" role="switch" aria-checked="false" aria-label="Local Events"></span>
    </li>
    <li class="category">
      <svg class="category-icon" width="40" height="30" viewBox="0 0 40 30" aria-hidden="true">
        <rect x="1.5" y="1.5" width="37" height="27" fill="none" stroke="var(--icon-grey)" stroke-width="2.5"/>
        <rect x="7" y="7" width="10" height="8" fill="var(--icon-grey)"/>
        <path d="M21 8h12M21 13h12M7 19h26M7 23h26" stroke="var(--icon-grey)" stroke-width="2"/>
      </svg>
      <span class="category-label">Weather Alerts</span>
      <span class="switch" role="switch" aria-checked="false" aria-label="Weather Alerts"></span>
    </li>
    <li class="category">
      <svg class="category-icon" width="40" height="30" viewBox="0 0 40 30" aria-hidden="true">
        <rect x="1.5" y="1.5" width="37" height="27" fill="none" stroke="var(--icon-grey)" stroke-width="2.5"/>
        <rect x="7" y="7" width="10" height="8" fill="var(--icon-grey)"/>
        <path d="M21 8h12M21 13h12M7 19h26M7 23h26" stroke="var(--icon-grey)" stroke-width="2"/>
      </svg>
      <span class="category-label">Local Deals</span>
      <span class="switch" role="switch" aria-checked="false" aria-label="Local Deals"></span>
    </li>
  </ul>
</div>
</body>
</html>
```